Quill Petal Loft Hair Salon needs a Webpage design

Quill Petal Loft in Englewood is looking to start their web page, url and business emails, we want to be able to upload pictures and videos on the website. we do blow outs , makeup, color, lash extension, gel manicures

Target Market(s)

everyone

Industry/Entity Type

Beauty Salon

Coding

Coded - Design and coding required

Number of Pages Required

5+ page

Font styles to use
Serif

Colors
ffcf3e
9d9d9d
000000
ffffff

Requirements
Must have
• about us, contact us, products, menu, location, gallery, press
Nice to have
• play video gallery

```html
<!DOCTYPE html>
<html lang="en">
<head>
<meta charset="utf-8">
<title>Quill Petal Loft Hair Salon</title>
<link href="https://fonts.googleapis.com/css2?family=Roboto:wght@300;400;500;700;900&family=Dancing+Script:wght@700&display=swap" rel="stylesheet">
<style>
:root{
  --gold:#ffcf3e;
  --gold-deep:#f5c021;
  --grey:#9d9d9d;
  --ink:#000000;
  --paper:#ffffff;
  --charcoal:#2b2b2b;
  --soft:#f4f4f4;
  --muted:#8a8a8a;
}
*{box-sizing:border-box;margin:0;padding:0}
html,body{width:1200px;height:3156px;overflow:hidden}
body{position:relative;background:var(--paper);font-family:"Roboto",Arial,sans-serif;color:var(--ink)}
.abs{position:absolute}

/* header */
.site-header{position:absolute;left:0;top:0;width:1200px;height:100px;background:var(--paper)}
.brand{position:absolute;left:72px;top:26px;font-family:"Roboto",Arial,sans-serif;font-weight:700;font-size:30px;color:var(--gold);display:flex;align-items:center;gap:10px}
.brand-dot{width:14px;height:14px;border-radius:50%;background:var(--gold)}
.call{position:absolute;right:72px;top:10px;display:flex;align-items:center;gap:8px;font-size:11px;color:var(--muted)}
.call strong{font-size:22px;color:var(--gold);font-weight:500}
.nav{position:absolute;right:72px;top:56px;display:flex;gap:6px;list-style:none}
.nav li{font-size:12px;font-weight:500;letter-spacing:.5px;color:#444;padding:7px 14px;border-radius:4px}
.nav li.active{background:var(--gold);color:var(--paper)}

/* hero */
.hero-photo{position:absolute;left:0;top:100px;width:1200px;height:740px;background:radial-gradient(ellipse at 50% 40%,#c79a6e 0%,#a77a52 22%,#cfcac6 48%,#e6e4e2 75%)}
.hero-band{position:absolute;left:0;top:648px;width:1200px;height:192px;background:var(--gold)}
.hero-brand{position:absolute;left:72px;top:592px;width:160px;height:168px;background:var(--gold-deep);padding:30px 18px}
.hero-brand span{display:block;font-weight:700;font-size:26px;line-height:32px;color:var(--ink)}
.slider-arrows{position:absolute;left:240px;top:600px;display:flex;gap:4px}
.slider-arrows div{width:54px;height:46px;background:#333;display:flex;align-items:center;justify-content:center}
.slider-arrows div:first-child{background:#555}
.hero-copy{position:absolute;left:265px;top:672px;width:860px;font-size:13px;line-height:21px;color:var(--paper)}
.btn-outline{position:absolute;left:265px;top:770px;width:124px;height:30px;border:2px solid var(--paper);border-radius:15px;color:var(--paper);font-size:11px;font-weight:700;letter-spacing:1px;display:flex;align-items:center;justify-content:center}

/* section title */
.section-title{position:absolute;left:0;width:1200px;text-align:center;font-size:26px;font-weight:700;letter-spacing:1px}
.section-title::after{content:"";display:block;width:50px;height:3px;background:var(--gold);margin:12px auto 0}

/* services */
.service{position:absolute;top:976px;width:320px;text-align:center}
.service-ring{width:208px;height:208px;margin:0 auto;border-radius:50%;border:6px solid var(--gold);padding:6px}
.service-photo{width:100%;height:100%;border-radius:50%}
.service h3{font-family:"Dancing Script",cursive;font-size:30px;margin-top:38px}
.service p{font-size:13px;line-height:19px;color:var(--muted);margin:10px auto 0;width:280px}
.btn-more{display:inline-block;margin-top:20px;background:var(--gold);color:var(--charcoal);font-size:11px;font-weight:700;letter-spacing:1px;padding:7px 26px;border-radius:14px}

/* counters */
.counters{position:absolute;left:0;top:1392px;width:1200px;height:308px;background:linear-gradient(90deg,#1c1c1c,#3a3330 45%,#1f1f1f)}
.counter{position:absolute;top:1500px;display:flex;align-items:flex-start;gap:20px}
.counter-num{font-size:56px;font-weight:300;color:var(--gold);line-height:60px}
.counter-label{font-size:15px;color:var(--paper);margin-top:12px}

/* gallery */
.filters{position:absolute;left:0;top:1806px;width:1200px;display:flex;justify-content:center;gap:8px;list-style:none}
.filters li{font-size:11px;font-weight:500;color:var(--muted);padding:6px 14px;border-radius:12px;letter-spacing:.5px}
.filters li.active{background:var(--gold);color:var(--paper)}
.tile{position:absolute;width:240px}

/* contact */
.contact{position:absolute;left:0;top:2640px;width:1200px;height:440px;background:var(--gold)}
.contact .section-title{color:var(--paper)}
.contact .section-title::after{background:var(--paper)}
.contact-card{position:absolute;left:72px;top:2780px;width:720px;height:228px;background:var(--charcoal)}
.map{position:absolute;left:0;top:0;width:416px;height:228px;background:linear-gradient(135deg,#e9e9e9,#cfcfcf)}
.map-label{position:absolute;left:12px;top:12px;width:180px;background:var(--paper);padding:8px 10px;font-size:10px;color:#555;line-height:14px}
.map-label b{display:block;font-size:11px;color:var(--ink)}
.contact-info{position:absolute;left:440px;top:22px;width:260px;color:var(--paper);font-size:12px;line-height:20px}
.contact-info p{margin-bottom:10px}
.socials{display:flex;gap:10px;margin-top:16px}
.socials span{width:28px;height:28px;border-radius:50%;background:#5a5a5a}
.contact-form{position:absolute;left:820px;top:2780px;width:308px}
.field{height:36px;background:var(--paper);margin-bottom:14px;padding:0 14px;font-size:12px;color:#aaa;display:flex;align-items:center}
.btn-submit{height:36px;background:var(--charcoal);color:var(--paper);font-size:12px;font-weight:700;letter-spacing:1px;display:flex;align-items:center;justify-content:center}

.site-footer{position:absolute;left:0;top:3080px;width:1200px;height:76px;background:#222;color:#bbb;font-size:12px;display:flex;align-items:center;justify-content:center}
</style>
</head>
<body>

<header class="site-header">
  <div class="brand"><span class="brand-dot"></span>Quill Petal Loft</div>
  <div class="call">
    <svg width="16" height="16" viewBox="0 0 24 24"><path fill="#ffcf3e" d="M6.6 10.8a15 15 0 0 0 6.6 6.6l2.2-2.2a1 1 0 0 1 1-.25 11.4 11.4 0 0 0 3.6.57 1 1 0 0 1 1 1V20a1 1 0 0 1-1 1A17 17 0 0 1 3 4a1 1 0 0 1 1-1h3.5a1 1 0 0 1 1 1c0 1.25.2 2.45.57 3.6a1 1 0 0 1-.25 1z"/></svg>
    CALL US <strong>031 555 0142</strong>
  </div>
  <ul class="nav">
    <li class="active">HOME</li><li>ABOUT</li><li>MENUS</li><li>PRODUCTS</li><li>LOCATIONS</li><li>PRESS BOOK NOW / CONTACT</li><li>SOCIAL</li>
  </ul>
</header>

<section class="hero">
  <div class="hero-photo" role="img" aria-label="Hero photo of a woman with long curly golden-brown hair"></div>
  <div class="hero-band"></div>
  <div class="hero-brand"><span>Quill</span><span>Petal</span><span>Loft</span></div>
  <div class="slider-arrows">
    <div><svg width="14" height="14" viewBox="0 0 14 14"><path d="M9 2 4 7l5 5" stroke="#fff" stroke-width="2" fill="none"/></svg></div>
    <div><svg width="14" height="14" viewBox="0 0 14 14"><path d="M5 2l5 5-5 5" stroke="#fff" stroke-width="2" fill="none"/></svg></div>
  </div>
  <p class="hero-copy">At Quill Petal Loft we specialise in blow outs, makeup, colour, lash extensions and gel manicures. Our stylists listen first, then shape every look around your hair, your face and your day. Walk in tired and walk out ready, with care that feels personal from the first wash to the final finish.</p>
  <div class="btn-outline">READ MORE</div>
</section>

<section class="services">
  <h2 class="section-title" style="top:914px">OUR SERVICES</h2>
  <div class="service" style="left:80px">
    <div class="service-ring"><div class="service-photo" role="img" aria-label="Hair cutting with scissors" style="background:linear-gradient(135deg,#b98a55,#8a5d33)"></div></div>
    <h3>Hair Cutting</h3>
    <p>Precision cuts shaped to your features, finished with a smooth blow out.</p>
    <span class="btn-more">MORE</span>
  </div>
  <div class="service" style="left:440px">
    <div class="service-ring"><div class="service-photo" role="img" aria-label="Hair styling with a straightener" style="background:linear-gradient(135deg,#3a2a22,#7a5a48)"></div></div>
    <h3>Hair Style</h3>
    <p>Waves, updos and sleek finishes styled for evenings, weddings and everyday.</p>
    <span class="btn-more">MORE</span>
  </div>
  <div class="service" style="left:800px">
    <div class="service-ring"><div class="service-photo" role="img" aria-label="Close view of coloured hair" style="background:linear-gradient(135deg,#a0622f,#5c3417)"></div></div>
    <h3>Hair Colour</h3>
    <p>Rich colour, soft highlights and glossing treatments that keep hair healthy.</p>
    <span class="btn-more">MORE</span>
  </div>
</section>

<section>
  <div class="counters" role="img" aria-label="Dark salon background photo"></div>
  <div class="counter" style="left:136px">
    <div><div class="counter-num">754</div><div class="counter-label">Happy People</div></div>
    <svg width="48" height="48" viewBox="0 0 48 48"><circle cx="24" cy="24" r="20" fill="none" stroke="#fff" stroke-width="3"/><circle cx="17" cy="19" r="2.5" fill="#fff"/><circle cx="31" cy="19" r="2.5" fill="#fff"/><path d="M15 29q9 8 18 0" stroke="#fff" stroke-width="3" fill="none"/></svg>
  </div>
  <div class="counter" style="left:400px">
    <div><div class="counter-num">984</div><div class="counter-label">People Like</div></div>
    <svg width="48" height="48" viewBox="0 0 48 48"><path d="M24 40 8 24a9 9 0 0 1 16-11 9 9 0 0 1 16 11z" fill="none" stroke="#fff" stroke-width="3"/></svg>
  </div>
  <div class="counter" style="left:668px">
    <div><div class="counter-num">106</div><div class="counter-label">Award Won</div></div>
    <svg width="48" height="48" viewBox="0 0 48 48"><path d="M24 5 40 10v12c0 10-7 17-16 21C15 39 8 32 8 22V10z" fill="none" stroke="#fff" stroke-width="3"/><path d="M24 5 8 10v12c0 10 7 17 16 21z" fill="#fff"/></svg>
  </div>
  <div class="counter" style="left:936px">
    <div><div class="counter-num">469</div><div class="counter-label">Cup Of Coffee</div></div>
    <svg width="48" height="48" viewBox="0 0 48 48"><path d="M8 16h26v12a10 10 0 0 1-10 10h-6A10 10 0 0 1 8 28z" fill="#fff"/><path d="M34 19h3a5 5 0 0 1 0 10h-3" stroke="#fff" stroke-width="3" fill="none"/><path d="M6 42h30" stroke="#fff" stroke-width="3"/></svg>
  </div>
</section>

<section class="gallery">
  <h2 class="section-title" style="top:1754px">VIEW GALLERY</h2>
  <ul class="filters">
    <li class="active">ALL</li><li>CUTTING</li><li>COLORING</li><li>CONDITIONING</li><li>STYLING</li><li>SHAMPOOING</li>
  </ul>
  <div class="tile" role="img" aria-label="Portrait with long straight dark hair" style="left:72px;top:1872px;height:368px;background:linear-gradient(160deg,#c9b8aa,#4a2e22)"></div>
  <div class="tile" role="img" aria-label="Portrait with braided dark hair" style="left:72px;top:2272px;height:240px;background:linear-gradient(160deg,#2a2a2a,#6b5548)"></div>
  <div class="tile" role="img" aria-label="Portrait with an elegant dark updo" style="left:344px;top:1872px;height:400px;background:linear-gradient(160deg,#1d1d1d,#4b3d36)"></div>
  <div class="tile" role="img" aria-label="Portrait with long blonde waves" style="left:344px;top:2304px;height:236px;background:linear-gradient(160deg,#222,#c9a06a)"></div>
  <div class="tile" role="img" aria-label="Portrait with soft blonde curls" style="left:616px;top:1872px;height:288px;background:linear-gradient(160deg,#e3ddd6,#b08a5f)"></div>
  <div class="tile" role="img" aria-label="Portrait with voluminous copper curls" style="left:616px;top:2192px;height:336px;background:linear-gradient(160deg,#f0ece8,#c0582a)"></div>
  <div class="tile" role="img" aria-label="Portrait with a blonde updo" style="left:888px;top:1872px;height:352px;background:linear-gradient(160deg,#e6e2dc,#b69462)"></div>
  <div class="tile" role="img" aria-label="Portrait with long brown curls" style="left:888px;top:2256px;height:284px;background:linear-gradient(160deg,#ebe6e1,#6e4a34)"></div>
</section>

<section class="contact">
  <h2 class="section-title" style="top:68px">CONTACT US</h2>
</section>
<div class="contact-card">
  <div class="map" role="img" aria-label="Street map showing the salon location">
    <div class="map-label"><b>QUILL PETAL LOFT</b>48 Larkspur Avenue, Englewood</div>
  </div>
  <div class="contact-info">
    <p>48 Larkspur Avenue,<br>Englewood NJ 07631</p>
    <p>Phone : +1 201 555 0187<br>Email : info@quillpetalloft.com</p>
    <div class="socials"><span></span><span></span><span></span><span></span></div>
  </div>
</div>
<form class="contact-form">
  <div class="field">Name</div>
  <div class="field">Email Address</div>
  <div class="field">Phone No</div>
  <div class="btn-submit">SUBMIT HERE</div>
</form>

<footer class="site-footer">Copyright © 2016, Quill Petal Loft. All Right Reserved.</footer>

</body>
</html>
```